Stationery Design Project for Nimbora, Chicago

Nimbora, a street parking application which helps car drivers find a street parking spot by offering an ideal path along which to look for parking. This path is calculated by our algorithm based on data (e.g. historical data, baseball games schedule, etc.). Along this path the driver will find a spot and will also save 70% of the search time. Customer we target is reg. between 21 and 45 yo.

We envision something young, fresh, bright and original. Slightly abstract maybe. It should represent the idea and elements of finding street parking in the city, e.g. car(s), parking spot, people, city, etc. (just ideas!).

Logo is attached.

Requirement:
- Business Cards (2 Sided Full Color CMYK)
- Letterhead (1 Sided Full Color CMYK)
- Envelope (1 Sided Full Color CMYK)
- Sticker (1 Sided Full Color CMYK), round with a 2inch diameter.

Reason: We're starting to get more and more designs and need more time to look into all of them. Very exciting!! Thanks to everybody!

Hi all, we're in the process of selecting our favs. Though choices!!! Really good submissions. Will keep you posted and sorry for the delay.

Target Market(s)

Car drivers and owners between 21 and 45

Industry/Entity Type

Parking

Requirements
Must have
• Sticker should be round and include company URL nimbora.com and the new logo which we will attach soon.
Should not have
• Should not be too serious or boring.

```html
<!DOCTYPE html>
<html lang="en">
<head>
<meta charset="utf-8">
<title>Nimbora Business Card</title>
<link rel="stylesheet" href="https://fonts.googleapis.com/css2?family=Open+Sans:wght@400;600;700&display=swap">
<style>
  :root {
    --page-bg: #ececec;
    --card-bg: #ffffff;
    --band-top: #2e3d9a;
    --band-bottom: #29a4e2;
    --rule: #2b2b2b;
    --ink: #231f20;
    --text-grey: #4a4a4a;
    --brand-blue: #1f7fc4;
    --name-blue: #2a6db5;
    --soft-blue: #e1ecf6;
    --url-grey: #555555;
  }
  * { box-sizing: border-box; margin: 0; padding: 0; }
  html, body {
    width: 1200px; height: 758px; overflow: hidden;
    background: var(--page-bg);
    font-family: "Open Sans", Arial, sans-serif;
  }
  .canvas { position: relative; width: 1200px; height: 758px; }
  .card {
    position: absolute; top: 236px;
    width: 500px; height: 286px;
    background: var(--card-bg);
    border-radius: 22px;
    overflow: hidden;
    box-shadow: 0 4px 14px rgba(0,0,0,0.15);
  }
  .card-front { left: 60px; }
  .card-back { left: 640px; }

  .side-band {
    position: absolute; left: 0; top: 0; bottom: 0; width: 82px;
    background: linear-gradient(180deg, var(--band-top), var(--band-bottom));
  }
  .side-rule {
    position: absolute; left: 90px; top: 0; bottom: 0; width: 2px;
    background: var(--rule);
  }
  .brand-dot {
    position: absolute; left: 30px; top: 40px;
    width: 84px; height: 84px; border-radius: 50%;
    background: var(--brand-blue);
  }
  .brand-name {
    position: absolute; left: 130px; top: 44px;
    font-size: 58px; font-weight: 700; color: var(--ink);
    letter-spacing: -1px; line-height: 1;
  }
  .contact-icons {
    position: absolute; left: 44px; top: 0; width: 20px; height: 286px;
  }
  .contact {
    position: absolute; left: 112px; top: 150px;
    font-size: 13px; color: var(--text-grey); line-height: 16px;
  }
  .contact-address { margin-bottom: 18px; }
  .holder-mark {
    position: absolute; left: 348px; top: 108px;
    width: 110px; height: 110px; border-radius: 50%;
    background: var(--soft-blue);
  }
  .holder {
    position: absolute; left: 340px; top: 140px; width: 140px; text-align: right;
  }
  .holder-name { font-size: 19px; font-weight: 700; color: var(--name-blue); }
  .holder-title { font-size: 13px; color: var(--text-grey); }

  .back-brand {
    position: absolute; left: 0; right: 0; top: 58px;
    display: flex; align-items: center; justify-content: center; gap: 20px;
  }
  .back-dot {
    width: 130px; height: 130px; border-radius: 50%;
    background: var(--brand-blue);
  }
  .back-name { font-size: 40px; font-weight: 700; color: var(--ink); letter-spacing: -1px; }
  .back-url {
    position: absolute; left: 0; right: 0; top: 218px; text-align: center;
    font-size: 24px; font-weight: 700; color: var(--url-grey); letter-spacing: 4px;
  }
</style>
</head>
<body>
<div class="canvas">
  <section class="card card-front">
    <div class="side-band"></div>
    <div class="side-rule"></div>
    <div class="brand-dot"></div>
    <div class="brand-name">nimbora</div>

    <svg class="contact-icons" viewBox="0 0 20 286" aria-hidden="true">
      <!-- home -->
      <path d="M10 152 L3 158 H5 V164 H9 V160 H11 V164 H15 V158 H17 Z" fill="#fff"/>
      <!-- phone -->
      <circle cx="10" cy="204" r="5" fill="none" stroke="#fff" stroke-width="1.5"/>
      <path d="M8 201 Q7 204 10 207" fill="none" stroke="#fff" stroke-width="1.5"/>
      <!-- mobile -->
      <rect x="7" y="215" width="6" height="10" rx="1" fill="#fff"/>
      <!-- mail -->
      <rect x="5" y="232" width="10" height="7" fill="#fff"/>
      <path d="M5 232 L10 236 L15 232" fill="none" stroke="#2aa0dc" stroke-width="1"/>
      <!-- globe -->
      <circle cx="10" cy="252" r="4.5" fill="#fff"/>
      <path d="M5.5 252 H14.5 M10 247.5 V256.5" stroke="#2aa4e2" stroke-width="0.8"/>
    </svg>

    <div class="contact">
      <p class="contact-address">Complex name, Street name<br>City, State, zip code</p>
      <p>123-456-789</p>
      <p>123-456-789</p>
      <p>hello@nimbora.com</p>
      <p>www.nimbora.com</p>
    </div>

    <div class="holder-mark"></div>
    <div class="holder">
      <p class="holder-name">Your Name</p>
      <p class="holder-title">Title</p>
    </div>
  </section>

  <section class="card card-back">
    <div class="back-brand">
      <div class="back-dot"></div>
      <div class="back-name">nimbora</div>
    </div>
    <p class="back-url">www.nimbora.com</p>
  </section>
</div>
</body>
</html>
```